Quorvane Capital LLC

Need Professional Business cards for New Investment Fund

Target Market(s)

High Quality investors

Industry/Entity Type

Financial

Contact Information for Business Card

Phone Number +1 555 284 6190
Name Lukas Varenko
Title Fund Manager
email lv@FundQuorvane.com
Website www.FundQuorvane.com

Colors

Designer to choose colors to be used in the design.

Requirements
Must have
• Must have our Logo and all of the above. Must be made so lettering and loge can be raised

```html
<!DOCTYPE html>
<html lang="en">
<head>
<meta charset="UTF-8">
<title>Quorvane Capital LLC — Business Card</title>
<link rel="stylesheet" href="https://fonts.googleapis.com/css2?family=Roboto:wght@400;500;700&display=swap">
<style>
  :root {
    --backdrop: #3a3a3a;
    --card: #232323;
    --lime: #8cc614;
    --white: #f4f4f4;
    --silver: #9a9a9a;
  }
  * { margin: 0; padding: 0; box-sizing: border-box; }
  html, body { width: 799px; height: 1200px; overflow: hidden; }
  body {
    background: var(--backdrop);
    font-family: "Roboto", sans-serif;
    position: relative;
  }
  .card {
    position: absolute;
    left: 50px;
    width: 700px;
    height: 400px;
    background: var(--card);
    border-radius: 4px;
    box-shadow: 0 10px 28px rgba(0,0,0,.45);
    overflow: hidden;
  }
  .card--front { top: 90px; }
  .card--back { top: 690px; }

  .front-wordmark {
    position: absolute;
    inset: 0;
    display: flex;
    align-items: center;
    justify-content: center;
    font-size: 44px;
    font-weight: 500;
    letter-spacing: 4px;
    color: var(--silver);
    text-transform: uppercase;
  }

  .accent-arc {
    position: absolute;
    left: -30px;
    top: 28px;
    width: 60px;
    height: 60px;
    border-radius: 50%;
    background: var(--lime);
  }
  .holder {
    position: absolute;
    left: 70px;
    top: 36px;
  }
  .holder-name {
    color: var(--lime);
    font-size: 26px;
    font-weight: 700;
    line-height: 30px;
  }
  .holder-title {
    color: var(--white);
    font-size: 15px;
    margin-top: 4px;
  }
  .contacts {
    position: absolute;
    left: 40px;
    top: 200px;
    list-style: none;
    color: var(--white);
    font-size: 17px;
    line-height: 24px;
  }
  .contacts li { display: flex; align-items: center; gap: 12px; }
  .contacts svg { width: 14px; height: 14px; flex: none; }
  .icon-fill { fill: var(--lime); }
  .icon-line { fill: none; stroke: var(--lime); stroke-width: 1.4; }
  .address {
    position: absolute;
    left: 40px;
    top: 280px;
    color: var(--white);
    font-size: 17px;
    line-height: 24px;
    font-style: normal;
  }
  .brand {
    position: absolute;
    right: 50px;
    bottom: 50px;
    display: flex;
    align-items: center;
    gap: 10px;
    color: var(--white);
    font-size: 24px;
    font-weight: 500;
    letter-spacing: 2px;
    text-transform: uppercase;
  }
  .brand-dot {
    width: 14px;
    height: 14px;
    border-radius: 50%;
    background: var(--lime);
  }
</style>
</head>
<body>
  <section class="card card--front">
    <div class="front-wordmark">Quorvane</div>
  </section>

  <section class="card card--back">
    <div class="accent-arc"></div>
    <div class="holder">
      <div class="holder-name">Lukas Varenko</div>
      <div class="holder-title">Fund Manager</div>
    </div>
    <ul class="contacts">
      <li>
        <svg viewBox="0 0 14 14" aria-hidden="true"><path class="icon-fill" d="M3 1l2.5 3-1.5 1.5c.8 1.8 2.2 3.2 4 4L9.5 8 12.5 10.5 11 13C6 13 1 8 1 3z"/></svg>
        <span>+1 555 284 6190</span>
      </li>
      <li>
        <svg viewBox="0 0 14 14" aria-hidden="true"><rect class="icon-line" x="1.2" y="3" width="11.6" height="8"/><path class="icon-line" d="M1.5 3.5L7 8l5.5-4.5"/></svg>
        <span>lv@FundQuorvane.com</span>
      </li>
      <li>
        <svg viewBox="0 0 14 14" aria-hidden="true"><circle class="icon-line" cx="7" cy="7" r="5.6"/><ellipse class="icon-line" cx="7" cy="7" rx="2.4" ry="5.6"/><path class="icon-line" d="M1.4 7h11.2"/></svg>
        <span>www.FundQuorvane.com</span>
      </li>
    </ul>
    <address class="address">14 Alder Row<br>Fairlake, NJ, 07990</address>
    <div class="brand">
      <span class="brand-dot"></span>
      <span>Quorvane</span>
    </div>
  </section>
</body>
</html>
```